Manufacturer of prepared Persian ready meals needs a product concept design

I need a product concept design for a new company based in the UK called 'Valdren Kitchen Ltd'.
The winner will potentially be selected to produce prototype designs for our other products.
For this project, the product will be called "Ghormeh Sabzi". This needs to be on the design to let consumers know what it is.
Whilst still in the concept stage, the aim of the company is to produce refrigerated microwaveable / oven Persian ready meal for retail supermarket consumers, and may also have an online platform for direct to consumer sales.
I have provided quite a few competitor examples of products.
I would like the product in a black or clear round bowl. It will be split into two sections (Half stew / Half rice) by the sleeve, which you are designing. I would like the food to be visible on either side of the label, so the consumer knows what they are eating.
The logo is provided within the file attachments and needs to be on prominent display on the pouch.
The mission for Valdren Kitchen Ltd brand is:
"Bringing 2,500 years of scented history to your table".
This needs to be present on the sleeve.
The product needs to represent the ethnicity of the brand throughout the design, and the same font to be used throughout.
Persian architecture was filled with a wide range of vibrant colours and has been engineered to stand the test of time, so I would like that to be incorporated into the product design (see attached examples of Persian geometry).
Alternatively Persian carpets are world renowned for their quality, so examples of this could be displayed on the packaging.
These will have to be artistically interpreted to avoid potential copyright; I am looking for individual artistic design.
It needs to represent a super quality, royalty & decadence throughout, and stand out on the shelves to the consumer above all the other competitor products.
To comply with food standards, the sleeve must have a nutritional label on display. I have attached a generic example for you to use. You may create your own representation of it.
Ghormeh Sabzi is a natural source of fibre, high in protein, gluten and dairy free, so I would like this displayed on the sleeve, as well as the the words:
- Traditionally rich in aromatic herbs, tender slow cooked lamb, red kidney beans & dried limes
- One of the oldest dishes in Persian history
You can find pictures of the food provided in the files. Note, these are not my pictures, but give you an idea of what will be provided inside.
Some designers have uploaded the same design up to 5 times, others twice. Only 18 have been uploaded, but it says 20, so I think 2 have been removed?

```html
<!DOCTYPE html>
<html lang="en">
<head>
<meta charset="utf-8">
<title>Valdren Kitchen – Ghormeh Sabzi sleeve</title>
<link href="https://fonts.googleapis.com/css2?family=Cabin:ital,wght@0,400;0,500;0,600;1,400;1,500&display=swap" rel="stylesheet">
<style>
  :root {
    --page: #ffffff;
    --sleeve: #35431c;
    --sleeve-edge: #2c3816;
    --lime: #8cc63f;
    --ornament-dark: #4f6a1f;
    --ornament-gold: #d9d23a;
    --text: #f4f4ef;
    --tab-energy: #f3f3f0;
    --tab-fat: #a9b79b;
    --tab-sugars: #8cc63f;
    --tab-salt: #f07f2a;
    --tab-sat: #e8254b;
    --tab-ink: #333333;
  }
  * { margin: 0; padding: 0; box-sizing: border-box; }
  html, body { width: 1200px; height: 1151px; overflow: hidden; background: var(--page); }
  body { position: relative; font-family: "Cabin", sans-serif; color: var(--text); }

  .sleeve {
    position: absolute; left: 346px; top: 80px; width: 467px; height: 1012px;
    background: var(--sleeve);
    box-shadow: inset 0 0 0 1px var(--sleeve-edge);
    overflow: hidden;
  }
  .ornament { position: absolute; left: 35px; width: 396px; display: block; }
  .ornament--top { top: 0; height: 135px; }
  .ornament--bottom { bottom: 0; height: 130px; }

  .brand { position: absolute; top: 165px; left: 0; width: 100%; text-align: center; }
  .brand__mark { width: 120px; height: 120px; margin: 0 auto 50px; background: var(--lime); }
  .brand__name {
    font-weight: 500; font-size: 36px; letter-spacing: 14px; line-height: 46px;
    color: var(--text); padding-left: 14px;
  }

  .tagline {
    position: absolute; top: 478px; width: 100%; text-align: center;
    font-style: italic; font-size: 17px; line-height: 23px;
  }
  .product-name {
    position: absolute; top: 543px; width: 100%; text-align: center;
    font-style: italic; font-weight: 500; font-size: 40px; line-height: 48px; color: var(--lime);
  }
  .weight {
    position: absolute; top: 612px; width: 100%; text-align: center;
    font-style: italic; font-size: 28px; line-height: 34px;
  }
  .weight small { font-size: 16px; }
  .description {
    position: absolute; top: 678px; width: 100%; text-align: center;
    font-style: italic; font-size: 12px; line-height: 21px;
  }

  .nutrition { position: absolute; top: 766px; left: 0; width: 100%; text-align: center; }
  .nutrition__intro { font-style: italic; font-size: 10px; line-height: 14px; margin-bottom: 3px; }
  .nutrition__tabs { display: flex; justify-content: center; gap: 1px; }
  .tab {
    width: 44px; height: 58px; border-radius: 22px 22px 0 0;
    color: var(--tab-ink); font-size: 8px; padding-top: 6px; line-height: 1.15;
    display: flex; flex-direction: column; align-items: center;
  }
  .tab__label { font-weight: 600; font-size: 8.5px; }
  .tab__value { margin-top: 3px; font-size: 9px; }
  .tab__level {
    background: #fff; border-radius: 3px; font-weight: 600; font-size: 6.5px;
    padding: 0 5px; margin-top: 1px;
  }
  .tab__ri { margin-top: auto; font-weight: 600; font-size: 7px; padding-bottom: 2px; }
  .tab--energy { background: var(--tab-energy); }
  .tab--energy .tab__value { font-size: 7.5px; margin-top: 2px; }
  .tab--fat { background: var(--tab-fat); }
  .tab--sugars { background: var(--tab-sugars); }
  .tab--salt { background: var(--tab-salt); }
  .tab--sat { background: var(--tab-sat); }
  .tab--sat .tab__label { font-size: 7px; }
  .nutrition__note { font-style: italic; font-size: 7px; line-height: 10px; margin-top: 3px; }
</style>
</head>
<body>
  <section class="sleeve">
    <svg class="ornament ornament--top" viewBox="0 0 396 135" role="img" aria-label="Ornate Persian medallion border in lime, gold and white">
      <defs>
        <linearGradient id="ornTop" x1="0" y1="0" x2="0" y2="1">
          <stop offset="0" stop-color="#d9d23a"/>
          <stop offset="0.5" stop-color="#8cc63f"/>
          <stop offset="1" stop-color="#4f6a1f"/>
        </linearGradient>
      </defs>
      <path d="M0 0 H396 Q370 30 330 45 Q290 90 198 135 Q106 90 66 45 Q26 30 0 0 Z" fill="url(#ornTop)"/>
    </svg>

    <div class="brand">
      <div class="brand__mark"></div>
      <div class="brand__name">VALDREN<br>KITCHEN</div>
    </div>

    <p class="tagline">Bringing 2,500 years of<br>scented history to your table</p>
    <h1 class="product-name">Ghormeh Sabzi</h1>
    <p class="weight">400<small>g</small></p>
    <p class="description">Traditionally rich in aromatic herbs, Tender slow cooked lamb,<br>Red kidney beans &amp; dried limes, One of the oldest dishes in Persian history.</p>

    <div class="nutrition">
      <p class="nutrition__intro">Each serving (150g) contains</p>
      <div class="nutrition__tabs">
        <div class="tab tab--energy"><span class="tab__label">Energy</span><span class="tab__value">1046kJ<br>250kcal</span><span class="tab__ri">13%</span></div>
        <div class="tab tab--fat"><span class="tab__label">Fat</span><span class="tab__value">3.0g</span><span class="tab__level">LOW</span><span class="tab__ri">4%</span></div>
        <div class="tab tab--sugars"><span class="tab__label">Sugars</span><span class="tab__value">34g</span><span class="tab__level">LOW</span><span class="tab__ri">38%</span></div>
        <div class="tab tab--salt"><span class="tab__label">Salt</span><span class="tab__value">0.9g</span><span class="tab__level">HIGH</span><span class="tab__ri">15%</span></div>
        <div class="tab tab--sat"><span class="tab__label">Saturates</span><span class="tab__value">1.3g</span><span class="tab__level">MED</span><span class="tab__ri">7%</span></div>
      </div>
      <p class="nutrition__note">of an adult's reference intake<br>Typical values (as sold) per 100g: 697kJ/ 167kcal</p>
    </div>

    <svg class="ornament ornament--bottom" viewBox="0 0 396 130" role="img" aria-label="Ornate Persian medallion border in lime, gold and white">
      <defs>
        <linearGradient id="ornBottom" x1="0" y1="1" x2="0" y2="0">
          <stop offset="0" stop-color="#d9d23a"/>
          <stop offset="0.5" stop-color="#8cc63f"/>
          <stop offset="1" stop-color="#4f6a1f"/>
        </linearGradient>
      </defs>
      <path d="M0 130 H396 Q370 102 330 88 Q290 47 198 0 Q106 47 66 88 Q26 102 0 130 Z" fill="url(#ornBottom)"/>
    </svg>
  </section>
</body>
</html>
```